Website design for company that sells taximeters and has a taxi dispatch call center, webstore neede

Need a website with a shop with at least 20 articles, in two languages, possibly by using a purchased theme (not purchased yet).The company provides equipments and dispatch solutions for taxi companies. Typical yellow and black theme

Target Market(s)

Taxi companies

Industry/Entity Type

Taxi

Number of Pages Required

3 page

Font styles to use
Sans Serif

Colors
fbed22
000000

Requirements
Must have
• - webstore for at least 20 articles
• - Documents folder where to put pdf material related to taximeters
• - contact form message submission
Nice to have
• Feedback section
Should not have
• Blogs,

```html
<!DOCTYPE html>
<html lang="en">
<head>
<meta charset="utf-8">
<title>Fareline – Taximeters &amp; Dispatch</title>
<link rel="stylesheet" href="https://fonts.googleapis.com/css2?family=Montserrat:wght@400;500;600;700&family=Open+Sans:wght@300;400;600;700&display=swap">
<style>
:root{
  --yellow:#f1c53a;
  --ink:#141414;
  --text:#333;
  --muted:#8a8a8a;
  --line:#e6e6e6;
  --soft:#f5f5f5;
  --white:#fff;
  --night:#1c1a18;
}
*{box-sizing:border-box;margin:0;padding:0}
html,body{width:1200px;height:2553px;overflow:hidden}
body{position:relative;background:var(--white);font-family:"Open Sans",sans-serif;color:var(--text)}
.abs{position:absolute}

/* header */
.brand{left:150px;top:14px;font-family:"Montserrat",sans-serif;font-weight:700;font-size:25px;color:var(--yellow);letter-spacing:1px}
.nav{left:383px;top:21px;display:flex;gap:10px;font-family:"Montserrat",sans-serif;font-weight:600;font-size:10.5px;color:var(--ink)}
.nav .active{color:var(--yellow)}
.head-phone{left:754px;top:17px;display:flex;align-items:center;gap:10px;font-family:"Montserrat",sans-serif;font-weight:500;font-size:15px;color:var(--ink)}
.lang{left:888px;top:21px;font-size:10px;font-family:"Montserrat",sans-serif;color:var(--ink)}
.search{left:982px;top:14px;width:153px;height:27px;border:2px solid var(--yellow);border-radius:14px;padding-left:14px;font-size:11px;color:#bbb;line-height:23px}
.search svg{position:absolute;right:10px;top:5px}

/* hero */
.socials{left:176px;top:108px;display:flex;flex-direction:column;gap:14px}
.socials span{width:11px;height:11px;border-radius:50%;background:var(--ink);display:block}
.social-caption{left:118px;top:305px;transform:rotate(-90deg);font-family:"Montserrat",sans-serif;font-size:8px;font-weight:700;letter-spacing:1px;color:var(--ink);width:130px;text-align:center}
.hero-bar{left:238px;top:184px;width:330px;height:13px;background:var(--yellow)}
.hero-title{left:238px;top:152px;font-weight:700;font-size:33px;color:var(--ink);letter-spacing:-.5px}
.hero-sub{left:238px;top:203px;font-weight:300;font-size:31px;color:var(--ink)}
.hero-copy{left:240px;top:253px;font-size:13px;line-height:18px;color:var(--text)}
.btn-buy{left:240px;top:301px;width:111px;height:39px;border:2.5px solid var(--ink);font-family:"Montserrat",sans-serif;font-style:normal;font-weight:600;font-size:11px;letter-spacing:2px;text-align:center;line-height:34px;color:var(--ink)}
.hero-product{left:648px;top:153px;width:332px;height:188px;background:linear-gradient(#2a2a2a,#0e0e0e);border-radius:6px}
.slide-dots{left:1166px;top:224px}
.hero-divider{left:0;top:480px;width:1200px;height:1px;background:var(--line)}
.hero-marker{left:604px;top:438px;width:1px;height:42px;background:var(--yellow)}

/* deals */
.tag{left:243px;top:512px;background:var(--yellow);color:var(--white);font-size:7.5px;font-weight:700;padding:3px 6px;letter-spacing:.5px}
.deal-title{left:242px;top:535px;font-family:"Montserrat",sans-serif;font-size:21px;color:var(--ink);letter-spacing:1px}
.deal-title b{font-weight:700}
.deal-title small{font-size:7.5px;color:var(--muted);letter-spacing:.5px;margin-left:10px;font-weight:500}
.card{top:597px;width:222px;height:257px;border:1px solid #eee;background:var(--white);text-align:center}
.card .shot{margin:34px auto 0;width:140px;height:96px;border-radius:6px;background:linear-gradient(#5a5e63,#1d1f22)}
.card .rule{height:1px;background:#eee;margin-top:30px}
.card .name{font-size:10px;margin-top:15px;color:var(--text)}
.card .stars{color:var(--yellow);font-size:11px;letter-spacing:1px;margin-top:4px}
.card .price{font-size:13px;margin-top:2px;color:var(--text)}
.card .price s{font-size:10px;color:#bbb;margin-left:3px}
.pager{left:512px;top:938px;width:184px;height:29px;border:2px solid var(--yellow);border-radius:15px;font-family:"Montserrat",sans-serif;font-size:9px;color:var(--text);display:flex;justify-content:space-between;align-items:center;padding:0 22px}
.pager-hub{left:585px;top:933px;width:38px;height:38px;border-radius:50%;background:var(--ink)}

/* about */
.about{left:0;top:1026px;width:1200px;height:387px;background:var(--soft)}
.about-title{left:0;top:1098px;width:1200px;text-align:center;font-family:"Montserrat",sans-serif;font-weight:700;font-size:18px;letter-spacing:4px;color:var(--yellow)}
.about-copy{left:250px;top:1160px;width:700px;text-align:center;font-family:"Montserrat",sans-serif;font-weight:600;font-size:12px;letter-spacing:2.5px;line-height:26.5px;color:#555;text-transform:uppercase}
.about-rule{left:514px;top:1365px;width:163px;height:1px;background:var(--yellow)}

/* banner */
.banner{left:0;top:1413px;width:1200px;height:439px;background:radial-gradient(ellipse at 50% 40%,#6a3a22 0%,#2a1e18 45%,var(--night) 80%)}
.banner-text{left:0;top:1660px;width:1200px;text-align:center;font-family:"Montserrat",sans-serif;font-weight:700;font-size:20px;letter-spacing:3px;color:var(--white)}

/* testimonials */
.clients-title{left:0;top:1877px;width:1200px;text-align:center;font-family:"Montserrat",sans-serif;font-weight:600;font-size:19px;color:var(--ink)}
.quote{top:1942px;width:223px;height:183px;border:1px solid var(--line);text-align:center;padding:0 22px}
.quote .avatar{width:44px;height:44px;border-radius:50%;background:#cfcfcf;border:2px solid #eee;margin:19px auto 0}
.quote .who{font-family:"Montserrat",sans-serif;font-size:12px;margin-top:4px;color:var(--text)}
.quote p{font-size:8.5px;line-height:13px;color:var(--muted);margin-top:6px}
.q-dots{left:594px;top:2156px;display:flex;gap:4px}
.q-dots span{width:7px;height:7px;border-radius:50%;background:#ddd}
.q-dots span:first-child{background:var(--yellow)}

/* cta */
.cta{left:0;top:2216px;width:1200px;height:102px;background:var(--yellow)}
.cta-ask{left:192px;top:2253px;font-family:"Montserrat",sans-serif;font-weight:700;font-size:17px;color:var(--ink)}
.cta-ask span{color:var(--white);margin-left:8px}
.cta-phone{left:645px;top:2250px;display:flex;align-items:center;gap:12px;font-family:"Montserrat",sans-serif;font-weight:700;font-size:19px;color:var(--ink)}
.feedback{left:841px;top:2245px;width:155px;height:36px;border:2px solid var(--white);display:flex;align-items:center;justify-content:center;gap:10px;font-family:"Montserrat",sans-serif;font-weight:700;font-size:16px;color:var(--white);letter-spacing:1px}

/* footer */
.footer{left:0;top:2318px;width:1200px;height:235px;background:#0b0b0b}
.fcol{top:2358px;width:170px;font-size:9px;line-height:14px;color:#e8e8e8}
.fcol h4{font-family:"Montserrat",sans-serif;font-size:9px;font-weight:700;color:var(--white);margin-bottom:9px}
.fcol h4 span,.fcol .hl{color:var(--yellow)}
.f-icons{display:flex;gap:6px;margin-top:2px}
.f-icons span{width:9px;height:9px;border-radius:50%;background:#e8e8e8}
.f-rule{left:252px;top:2458px;width:706px;height:1px;background:#444}
.copy{left:252px;top:2470px;font-size:8px;color:#ddd}
.copy .hl{color:var(--yellow)}
</style>
</head>
<body>

<header>
  <div class="abs brand">FARELINE</div>
  <nav class="abs nav"><span class="active">HOME</span><span>SHOP</span><span>SERVICES</span><span>INSTALLERS</span><span>CONTACT US</span><span>JOIN US</span></nav>
  <div class="abs head-phone">
    <svg width="20" height="20" viewBox="0 0 24 24" fill="none" stroke="#141414" stroke-width="1.6"><path d="M5 3h4l2 5-2.5 1.5a11 11 0 0 0 6 6L16 13l5 2v4a2 2 0 0 1-2 2A17 17 0 0 1 3 5a2 2 0 0 1 2-2z"/></svg>
    555.010.4400
  </div>
  <div class="abs lang">ENG ▾</div>
  <div class="abs search">search
    <svg width="14" height="14" viewBox="0 0 24 24" fill="none" stroke="#ccc" stroke-width="2"><circle cx="10" cy="10" r="7"/><path d="M15 15l6 6"/></svg>
  </div>
</header>

<section class="hero">
  <div class="abs socials"><span></span><span></span><span></span><span></span><span></span></div>
  <div class="abs social-caption">GET IN TOUCH WITH SOCIALS</div>
  <div class="abs hero-bar"></div>
  <h1 class="abs hero-title">ORBIT M3</h1>
  <div class="abs hero-sub">BLUETOOTH TAXIMETER</div>
  <p class="abs hero-copy">Built in power supply and relay for toplights,<br>Built in signal divider.</p>
  <div class="abs btn-buy">BUY NOW</div>
  <div class="abs hero-product" role="img" aria-label="Product photo of a black taximeter with red fare display"></div>
  <svg class="abs slide-dots" width="14" height="34" viewBox="0 0 14 34"><circle cx="7" cy="7" r="5" fill="none" stroke="#f1c53a" stroke-width="1.5"/><circle cx="7" cy="7" r="2" fill="#f1c53a"/><circle cx="7" cy="27" r="3" fill="#f1c53a"/></svg>
  <div class="abs hero-marker"></div>
  <div class="abs hero-divider"></div>
</section>

<section class="deals">
  <div class="abs tag">QUALITY STANDARD</div>
  <h2 class="abs deal-title"><b>DEAL</b> OF THE WEEK/<small>EXCLUSIVE DISPATCH AND METER PRODUCTS</small></h2>
  <div class="abs card" style="left:248px">
    <div class="shot" role="img" aria-label="Product photo of a grey taximeter"></div>
    <div class="rule"></div>
    <div class="name">Ipsum dolor sit amet conipiscing</div>
    <div class="stars">★★★★★</div>
    <div class="price">485.50$<s>$729.20</s></div>
  </div>
  <div class="abs card" style="left:495px">
    <div class="shot" role="img" aria-label="Product photo of a dispatch radio with handset"></div>
    <div class="rule"></div>
    <div class="name">Ipsum dolor sit amet conipiscing</div>
    <div class="stars">★★★★★</div>
    <div class="price">456.50$<s>$589.20</s></div>
  </div>
  <div class="abs card" style="left:742px">
    <div class="shot" role="img" aria-label="Product photo of a slim taximeter with blue buttons"></div>
    <div class="rule"></div>
    <div class="name">Ipsum dolor sit amet conipiscing</div>
    <div class="stars">★★★★★</div>
    <div class="price">450.50$<s>$650.20</s></div>
  </div>
  <div class="abs pager"><span>&lt; PREV</span><span>NEXT &gt;</span></div>
  <div class="abs pager-hub">
    <svg width="38" height="38" viewBox="0 0 38 38" fill="#f1c53a"><circle cx="13" cy="13" r="2"/><circle cx="19" cy="13" r="2"/><circle cx="25" cy="13" r="2"/><circle cx="13" cy="19" r="2"/><circle cx="19" cy="19" r="2"/><circle cx="25" cy="19" r="2"/><circle cx="13" cy="25" r="2"/><circle cx="19" cy="25" r="2"/><circle cx="25" cy="25" r="2"/></svg>
  </div>
</section>

<section>
  <div class="abs about"></div>
  <svg class="abs" style="left:583px;top:1052px" width="34" height="22" viewBox="0 0 34 22" fill="none" stroke="#333" stroke-width="1.3"><rect x="13" y="1" width="8" height="3"/><path d="M9 9l3-5h10l3 5"/><rect x="2" y="9" width="30" height="8" rx="2"/><circle cx="9" cy="17" r="2.5"/><circle cx="25" cy="17" r="2.5"/></svg>
  <h2 class="abs about-title">WHO WE ARE</h2>
  <p class="abs about-copy">We supply the best meter &amp; dispatch<br>equipment for taxi vendors. Lorem ipsum dolor sit amet,<br>consectetuer adipiscing elit. Aenean commodo ligula eget dolor.<br>Aenean massa. Cum sociis natoque penatibus et magnis dis<br>parturient montes, nascetur ridiculus mus. Donec qu</p>
  <div class="abs about-rule"></div>
</section>

<section>
  <div class="abs banner" role="img" aria-label="Night photo of a lit taxi roof sign with blurred city lights"></div>
  <div class="abs banner-text">ALL TAXI NEEDS FOR DRIVERS AND FLEETS</div>
</section>

<section>
  <h2 class="abs clients-title">WHAT OUR CLIENTS SAY</h2>
  <div class="abs quote" style="left:252px">
    <div class="avatar" role="img" aria-label="Client portrait"></div>
    <div class="who">Ann Black</div>
    <p>Sed malesuada, neque quis tincidunt suscipit, lorem lectus rutrum lacus, a iaculis ipsum eros sed ipsum. Sed scelerisque massa ut nibh tincidunt, eget pellentesque.</p>
  </div>
  <div class="abs quote" style="left:494px">
    <div class="avatar" role="img" aria-label="Client portrait"></div>
    <div class="who">John Doe</div>
    <p>Sed malesuada, neque quis tincidunt suscipit, lorem lectus rutrum lacus, a iaculis ipsum eros sed ipsum. Sed scelerisque massa ut nibh tincidunt, eget pellentesque.</p>
  </div>
  <div class="abs quote" style="left:735px">
    <div class="avatar" role="img" aria-label="Client portrait"></div>
    <div class="who">Oliver Garden</div>
    <p>Sed malesuada, neque quis tincidunt suscipit, lorem lectus rutrum lacus, a iaculis ipsum eros sed ipsum. Sed scelerisque massa ut nibh tincidunt, eget pellentesque.</p>
  </div>
  <div class="abs q-dots"><span></span><span></span></div>
</section>

<section>
  <div class="abs cta"></div>
  <div class="abs cta-ask">HAVE A QUESTION?<span>FEEL FREE TO ASK...</span></div>
  <div class="abs cta-phone">
    <svg width="24" height="24" viewBox="0 0 24 24" fill="none" stroke="#fff" stroke-width="1.6"><path d="M5 3h4l2 5-2.5 1.5a11 11 0 0 0 6 6L16 13l5 2v4a2 2 0 0 1-2 2A17 17 0 0 1 3 5a2 2 0 0 1 2-2z"/></svg>
    555.010.8800
  </div>
  <div class="abs feedback">
    <svg width="26" height="18" viewBox="0 0 26 18" fill="none" stroke="#fff" stroke-width="2"><rect x="1" y="1" width="24" height="16"/><path d="M1 1l12 9 12-9"/></svg>
    FEEDBACK
  </div>
</section>

<footer>
  <div class="abs footer"></div>
  <div class="abs fcol" style="left:252px">
    <h4>ABOUT <span>FARELINE</span></h4>
    We provide quality dispatch and meter equipment for indecent taxi &amp; fleet vendors.
  </div>
  <div class="abs fcol" style="left:434px">
    <h4>CONTACT INFO</h4>
    Shop Office: (555) 014-2290<br>Customer service: (555) 014-7731<br>Email: <span class="hl">hello@fareline.example</span>
  </div>
  <div class="abs fcol" style="left:614px">
    <h4>HOURS OF SERVICE</h4>
    Monday - Friday: 09:00AM - 09:00PM<br>Saturday: 09:00AM - 07:00PM<br>Sunday: Closed
  </div>
  <div class="abs fcol" style="left:793px">
    <h4>LINK <span>US</span></h4>
    <div class="f-icons"><span></span><span></span><span></span><span></span><span></span></div>
  </div>
  <div class="abs f-rule"></div>
  <div class="abs copy">© 2018 <span class="hl">fareline.example</span> &nbsp;&nbsp;| Trademarks and brands are the property of their respective owners.</div>
</footer>

</body>
</html>
```